Redo our website for our Robotics company

We sell robotic equipment to the restaurant industry. Our current robot, is a cooking robot that cooks up to 15 lbs of food. We will provide a prior website as well as brand guidelines. We plan on using wordpress and take advantage of wordpress's visual (no code) editor.

Current website - https://kelvatrix88.com/ (please note we are only selling Tammo now and no longer selling Plavo+

We want someone to take our existing content and design the website as well as layout our content we provide. Here's a suggested site layout:

✅ KelvaTrix88 Website Wireframe / Site Map
1. Home

Purpose: Introduce Tammo, establish credibility, drive demo requests.

Sections:

Hero Section

Headline: “Meet Tammo — Your New Robotic Chef for High-Volume, Consistent Cooking.”

Sub-headline: Increase throughput. Reduce labor. Deliver perfect food every time.

CTA: Request a Demo + Watch Tammo Cook

Visual: Video loop or hero animation of Tammo in action.

How Tammo Works (3-4 steps)

Step cards: Load Ingredients → Select Recipe → Tammo Cooks → Serve

Icons and short explanations.

Key Benefits

Labor savings

Zero inconsistency

24/7 uptime

Throughput increases (30–50% faster)

Health & safety compliance

Who It’s For

QSR restaurants

Fast casual

Catering/commissaries

Ghost kitchens

Case Studies / Testimonials

Logo bar + quotes

“Tammo helped us reduce cooking times by 40%.”

Video Section

“Watch Tammo cook a full batch from start to finish.”

CTA Section

Big banner: Book a Demo

2. Product: “Meet Tammo”

Purpose: Deep dive into hardware, software, safety, reliability.

Sections:

Overview

What Tammo is

What tasks it automates

Where it fits in a kitchen

Hardware Features

High-temperature cooking chamber

Precision sensors

Automated stirring

Automated dispensing

Safety mechanisms (locking lids, auto-shutoff)

Software & AI

Recipe automation

IoT dashboard

Remote monitoring

Predictive maintenance

Specs Table

Dimensions

Power requirements

Capacity (lbs per batch)

Safety certifications

Gallery

Close-ups, installation photos, process shots

CTA: Request a Demo

3. Solutions

Purpose: Show that Tammo solves real operational problems.

Sub-pages or sections:

For Quick-Service Restaurants

Reduce labor cost

Speed up peak-hour demand

For Catering & Commissaries

Large-batch consistency

Automate repetitive cooking tasks

For High-Growth Chains

Replicable quality across multiple locations

Centralized recipe control

Each solution page includes:

A problem statement

How Tammo solves it

Metrics / KPIs

Relevant testimonial

CTA

4. ROI / Economics

Purpose: Sell the financial story clearly.

Sections:

Savings Calculator

Labor hours saved

Cost savings

Throughput increases

Food waste reduction

Before & After Comparison

Traditional kitchen vs. robotic kitchen

Sample ROI

“Payback in as little as 3–6 months.”

Download Full ROI Report (PDF)

5. Case Studies

Purpose: Social proof + real results.

Structure for each case study:

Customer background

Problem

Implementation

KPIs achieved

Labor savings

Consistency improvements

Cooking speed

Quote + photos/video

6. Pricing

Purpose: Start a commercial conversation.

Include:

Subscription model (monthly / annual)

Hardware leasing or purchase options

Installation + training

Support level

CTA to book a sales call

7. About

Purpose: Build trust.

Sections:

Mission statement

Founding team

Advisors/partners

“Why we built Tammo”

8. Resources

Purpose: SEO + education.

Subpages:

Blog (e.g., “The Future of Automated Kitchens”)

Whitepapers

Technical documentation

Product videos

9. Contact

General inquiry form

Sales contact

Support portal

Careers

```html
<!DOCTYPE html>
<html lang="en">
<head>
<meta charset="utf-8">
<title>KelvaTrix88 — Meet Tammo</title>
<link href="https://fonts.googleapis.com/css2?family=Montserrat:wght@600;700;800&family=Oswald:wght@400;500&family=Lora:wght@400&family=Poppins:wght@400;500;600&display=swap" rel="stylesheet">
<style>
:root{
  --orange:#f27a3c;
  --red:#e43a2b;
  --navy:#0b2c69;
  --navy-deep:#0a2456;
  --ink:#111827;
  --body:#333a46;
  --muted:#6b7280;
  --white:#ffffff;
  --mist:#eef1f5;
}
*{box-sizing:border-box;margin:0;padding:0}
html,body{width:1200px;height:4938px;overflow:hidden}
body{font-family:"Poppins",sans-serif;color:var(--ink);background:var(--white)}
section,header,footer{position:relative;width:1200px;overflow:hidden}
.wordmark{font-family:"Montserrat",sans-serif;font-weight:800;color:var(--red);letter-spacing:-.5px}
.section-title{font-family:"Montserrat",sans-serif;font-weight:800;font-size:38px;text-align:center;letter-spacing:.5px;color:var(--ink)}
.section-title .accent{color:var(--red)}
.title-rule{width:48px;height:3px;background:var(--navy);margin:18px auto 0}
.btn{display:inline-flex;align-items:center;justify-content:center;font-family:"Montserrat",sans-serif;font-weight:700;font-size:18px;border-radius:8px;height:52px;padding:0 22px}
.btn-solid{background:var(--orange);color:var(--white)}
.btn-outline{border:2px solid var(--orange);color:var(--orange)}

/* hero */
.hero{height:661px;background:linear-gradient(180deg,#2a2b2e 0%,#3b3c3f 40%,#1d1e20 100%)}
.hero-photo{position:absolute;inset:0;background:radial-gradient(ellipse at 50% 35%,rgba(120,118,112,.45),transparent 65%),linear-gradient(90deg,rgba(0,0,0,.35),rgba(0,0,0,0) 30%,rgba(0,0,0,0) 70%,rgba(0,0,0,.35))}
.nav{position:absolute;top:28px;left:35px;right:35px;display:flex;align-items:center;justify-content:space-between}
.nav .wordmark{font-size:30px}
.nav-links{display:flex;gap:22px;list-style:none;font-size:13px;color:var(--white)}
.nav-links li{padding:5px 10px}
.nav-links .current{background:var(--orange);border-radius:4px}
.hero-copy{position:absolute;top:310px;left:0;right:0;text-align:center;color:var(--white)}
.hero-copy h1{font-family:"Montserrat",sans-serif;font-weight:800;font-size:39px;line-height:52px}
.hero-copy h1 .accent{color:var(--orange)}
.hero-copy p{font-family:"Oswald",sans-serif;font-size:28px;margin-top:22px;font-weight:400}
.hero-ctas{display:flex;gap:20px;justify-content:center;margin-top:30px}
.hero-ctas .btn{width:200px}
.hero-ctas .btn-outline{width:232px}

/* how it works */
.how{height:681px;background:linear-gradient(180deg,#fff 0%,#fff 50%,#b3c3dd 100%)}
.how .section-title{padding-top:62px}
.card-row{position:absolute;left:151px;display:flex;gap:18px}
.step-card{width:211px;height:428px;background:var(--white);border-radius:6px;box-shadow:0 6px 18px rgba(10,36,86,.12);text-align:center;overflow:hidden}
.step-photo{height:243px;background:linear-gradient(160deg,#4a4d52,#1e2023)}
.step-icon{width:66px;height:66px;border-radius:50%;background:var(--navy);border:3px solid var(--white);box-shadow:0 0 0 3px var(--orange);margin:-33px auto 0;position:relative;display:flex;align-items:center;justify-content:center}
.step-card h3{font-family:"Oswald",sans-serif;font-weight:500;font-size:16px;color:var(--navy-deep);margin-top:20px}
.step-card p{font-family:"Lora",serif;font-size:12.5px;line-height:18px;color:var(--body);padding:10px 20px 0}

/* benefits */
.benefits{height:378px;background:linear-gradient(135deg,#0a2456,#0d3279 60%,#0a2456);color:var(--white)}
.benefits .section-title{color:var(--white);padding-top:42px}
.benefits .title-rule{background:var(--white)}
.benefit-list{position:absolute;top:168px;left:0;right:0;display:flex;justify-content:center;gap:0;list-style:none}
.benefit{width:196px;text-align:center}
.benefit-badge{width:96px;height:96px;border-radius:50%;background:var(--orange);margin:0 auto;display:flex;align-items:center;justify-content:center}
.benefit span{display:block;font-family:"Oswald",sans-serif;font-size:14px;margin-top:22px;line-height:22px;text-transform:uppercase}

/* audience */
.audience{height:552px}
.audience .section-title{padding-top:52px}
.audience-card{width:211px;height:307px;background:var(--white);border-radius:6px;box-shadow:0 6px 18px rgba(10,36,86,.12);text-align:center;overflow:hidden}
.audience-photo{height:243px}
.audience-card h3{font-family:"Oswald",sans-serif;font-weight:500;font-size:16px;color:var(--navy-deep);margin-top:20px}

/* testimonials */
.testimonials{height:738px;background:linear-gradient(180deg,#e9ecf0,#f7f8fa 60%,#e6e9ed)}
.testimonials .section-title{padding-top:56px}
.quote-card{width:288px;height:426px;background:var(--white);border-radius:8px;box-shadow:0 6px 18px rgba(10,36,86,.1);overflow:hidden}
.quote-photo{height:182px}
.quote-mark{font-family:"Montserrat",sans-serif;font-weight:800;font-size:58px;line-height:40px;color:var(--red);padding:18px 0 0 28px;height:52px}
.quote-card p{font-family:"Lora",serif;font-size:12.5px;line-height:18px;color:var(--body);padding:6px 28px 0 30px}
.author{display:flex;align-items:center;gap:14px;padding:20px 30px 0}
.avatar{width:40px;height:40px;border-radius:50%;background:linear-gradient(135deg,#c9b8a6,#8c7a68)}
.author b{display:block;font-family:"Lora",serif;font-weight:400;font-size:13px;color:var(--ink)}
.author small{font-family:"Lora",serif;font-size:11px;color:var(--muted)}
.dots{position:absolute;top:2940px;}
.pager{position:absolute;top:668px;left:0;right:0;display:flex;justify-content:center;gap:10px}
.pager i{width:11px;height:11px;border-radius:50%;border:1.5px solid var(--orange)}
.pager i.on{background:var(--orange)}

/* highlight quote */
.highlight{height:255px;background:var(--white);text-align:center}
.highlight .wordmark{font-size:28px;padding-top:78px}
.highlight blockquote{font-family:"Lora",serif;font-size:33px;color:var(--ink);margin-top:22px}
.arrow{position:absolute;top:110px}

/* video */
.video{height:688px;background:var(--mist)}
.video .section-title{padding-top:64px;line-height:52px}
.video-frame{position:absolute;top:222px;left:201px;width:796px;height:405px;border-radius:18px;background:linear-gradient(120deg,#2b3140,#4a5468 45%,#2c2f36);overflow:hidden}
.play{position:absolute;left:366px;top:171px;width:64px;height:64px;border-radius:50%;background:var(--red);display:flex;align-items:center;justify-content:center}

/* cta */
.cta{height:564px;background:linear-gradient(120deg,#0b2c69 0%,#143a82 50%,#0b2c69 100%);color:var(--white)}
.cta-product{position:absolute;left:201px;top:56px;width:250px;height:460px;background:linear-gradient(90deg,#2e3033,#6c7075 55%,#3a3c40);border-radius:10px}
.cta-copy{position:absolute;left:600px;top:96px;width:430px}
.cta-copy h2{font-family:"Montserrat",sans-serif;font-weight:800;font-size:44px;line-height:52px}
.cta-copy h2 .accent{color:var(--red)}
.cta-copy .rule{width:48px;height:3px;background:var(--white);margin:22px 0 28px}
.cta-copy p{font-family:"Lora",serif;font-size:16px;line-height:26px}
.cta-copy .btn{margin-top:40px;width:206px}

/* footer */
.site-footer{height:421px;background:#0d2a5f;color:var(--white)}
.site-footer .wordmark{position:absolute;left:153px;top:140px;font-size:36px}
.footer-col{position:absolute;top:58px}
.footer-col h4{font-family:"Montserrat",sans-serif;font-weight:700;font-size:14px;margin-bottom:14px}
.footer-col ul{list-style:none;font-size:12px;line-height:21px}
.contact-line{display:flex;gap:16px;font-size:12px;line-height:20px;margin-bottom:18px;align-items:flex-start}
.socials{display:flex;gap:8px}
.socials i{width:30px;height:30px;border-radius:50%;border:2px solid var(--white);display:block}
.footer-col .btn{height:42px;font-size:15px;width:176px;margin-top:30px}
.footer-rule{position:absolute;top:310px;left:153px;right:153px;height:1px;background:rgba(255,255,255,.3)}
.legal{position:absolute;top:356px;left:0;right:0;text-align:center;font-size:12px}
</style>
</head>
<body>

<header class="hero">
  <div class="hero-photo" role="img" aria-label="Kitchen line of Tammo cooking robots in action"></div>
  <nav class="nav">
    <span class="wordmark">KelvaTrix88</span>
    <ul class="nav-links">
      <li class="current">Home</li><li>Product</li><li>Solutions</li><li>ROI / Economics</li><li>Case Studies</li><li>Pricing</li><li>About Us</li><li>Resources</li><li>Contact</li>
    </ul>
  </nav>
  <div class="hero-copy">
    <h1><span class="accent">Meet Tammo</span> — Your New Robotic Chef<br>for High-Volume, Consistent Cooking.</h1>
    <p>Increase throughput. Reduce labor. Deliver perfect food every time.</p>
    <div class="hero-ctas">
      <a class="btn btn-solid">Request a Demo</a>
      <a class="btn btn-outline">Watch Tammo Cook</a>
    </div>
  </div>
</header>

<section class="how">
  <h2 class="section-title">HOW <span class="accent">TAMMO</span> WORKS</h2>
  <div class="title-rule"></div>
  <div class="card-row" style="top:192px">
    <article class="step-card">
      <div class="step-photo" role="img" aria-label="Ingredients being loaded into the cooking chamber"></div>
      <div class="step-icon"><svg width="34" height="34" viewBox="0 0 34 34" fill="none" stroke="#fff" stroke-width="2.4"><path d="M5 17h24v5a7 7 0 0 1-7 7h-10a7 7 0 0 1-7-7z"/><path d="M12 12c0-3 3-3 3-6M19 12c0-3 3-3 3-6"/></svg></div>
      <h3>LOAD INGREDIENTS</h3>
      <p>Lorem ipsum dolor sit amet, consectetur adipiscing elit, sed do eiusmod tempor incididunt</p>
    </article>
    <article class="step-card">
      <div class="step-photo" role="img" aria-label="Hand selecting a recipe on the touchscreen"></div>
      <div class="step-icon"><svg width="34" height="34" viewBox="0 0 34 34" fill="none" stroke="#fff" stroke-width="2.4"><rect x="8" y="5" width="18" height="24" rx="2"/><path d="M12 12h10M12 17h10M12 22h6"/></svg></div>
      <h3>SELECT RECIPE</h3>
      <p>Lorem ipsum dolor sit amet, consectetur adipiscing elit, sed do eiusmod tempor incididunt</p>
    </article>
    <article class="step-card">
      <div class="step-photo" role="img" aria-label="Tammo stirring food in its chamber"></div>
      <div class="step-icon"><svg width="34" height="34" viewBox="0 0 34 34" fill="none" stroke="#fff" stroke-width="2.4"><rect x="7" y="8" width="20" height="20" rx="2"/><circle cx="17" cy="18" r="4"/><path d="M11 5v3M23 5v3"/></svg></div>
      <h3>TAMMO COOKS</h3>
      <p>Lorem ipsum dolor sit amet, consectetur adipiscing elit, sed do eiusmod tempor incididunt</p>
    </article>
    <article class="step-card">
      <div class="step-photo" role="img" aria-label="Plated dish being served"></div>
      <div class="step-icon"><svg width="34" height="34" viewBox="0 0 34 34" fill="none" stroke="#fff" stroke-width="2.4"><path d="M6 24a11 11 0 0 1 22 0z"/><path d="M4 27h26M17 10v3"/></svg></div>
      <h3>SERVE</h3>
      <p>Lorem ipsum dolor sit amet, consectetur adipiscing elit, sed do eiusmod tempor incididunt</p>
    </article>
  </div>
</section>

<section class="benefits">
  <h2 class="section-title">BENEFITS</h2>
  <div class="title-rule"></div>
  <ul class="benefit-list">
    <li class="benefit"><div class="benefit-badge"><svg width="52" height="52" viewBox="0 0 52 52" fill="none" stroke="#fff" stroke-width="2.6"><circle cx="26" cy="26" r="20"/><path d="M12 40L40 12"/><path d="M30 19c-2-2-8-2-8 2s8 3 8 7-6 4-8 2M26 15v22"/></svg></div><span>Labor Savings</span></li>
    <li class="benefit"><div class="benefit-badge"><svg width="52" height="52" viewBox="0 0 52 52" fill="none" stroke="#fff" stroke-width="2.6"><circle cx="26" cy="18" r="5"/><circle cx="14" cy="24" r="4"/><circle cx="38" cy="24" r="4"/><path d="M16 40a10 10 0 0 1 20 0M6 40a8 8 0 0 1 10-8M46 40a8 8 0 0 0-10-8"/></svg></div><span>Zero Inconsistency</span></li>
    <li class="benefit"><div class="benefit-badge"><svg width="52" height="52" viewBox="0 0 52 52" fill="none" stroke="#fff" stroke-width="2.6"><path d="M44 26A18 18 0 1 1 38 12"/><path d="M38 6v7h-7"/><text x="15" y="31" fill="#fff" stroke="none" font-family="Oswald,sans-serif" font-size="14">24/7</text></svg></div><span>24/7 Uptime</span></li>
    <li class="benefit"><div class="benefit-badge"><svg width="52" height="52" viewBox="0 0 52 52" fill="none" stroke="#fff" stroke-width="2.6"><circle cx="30" cy="26" r="16"/><path d="M30 17v9l6 4M6 20h10M4 26h10M6 32h10"/></svg></div><span>Throughput Increases<br>(30–50% Faster)</span></li>
    <li class="benefit"><div class="benefit-badge"><svg width="52" height="52" viewBox="0 0 52 52" fill="none" stroke="#fff" stroke-width="2.6"><path d="M26 6l16 6v12c0 11-7 18-16 22-9-4-16-11-16-22V12z"/><path d="M19 26l5 5 9-10"/></svg></div><span>Health &amp; Safety<br>Compliance</span></li>
  </ul>
</section>

<section class="audience">
  <h2 class="section-title"><span class="accent">WHO</span> IT’S FOR</h2>
  <div class="title-rule"></div>
  <div class="card-row" style="top:178px">
    <article class="audience-card"><div class="audience-photo" role="img" aria-label="Quick-service burger and fries counter" style="background:linear-gradient(160deg,#c9863f,#7a3a1c)"></div><h3>QSR RESTAURANTS</h3></article>
    <article class="audience-card"><div class="audience-photo" role="img" aria-label="Fast casual dining room" style="background:linear-gradient(160deg,#8a5a34,#3a2518)"></div><h3>FAST CASUAL</h3></article>
    <article class="audience-card"><div class="audience-photo" role="img" aria-label="Catering plates being garnished" style="background:linear-gradient(160deg,#dfe3e0,#7f8b80)"></div><h3>CATERING/COMMISSARIES</h3></article>
    <article class="audience-card"><div class="audience-photo" role="img" aria-label="Stainless steel ghost kitchen" style="background:linear-gradient(160deg,#c5cbd2,#6d747c)"></div><h3>GHOST KITCHENS</h3></article>
  </div>
</section>

<section class="testimonials">
  <h2 class="section-title">TESTIMONIALS</h2>
  <div class="title-rule"></div>
  <div class="card-row" style="top:191px;gap:18px">
    <article class="quote-card">
      <div class="quote-photo" role="img" aria-label="Chefs working in a commercial kitchen" style="background:linear-gradient(160deg,#aab2ba,#4e565e)"></div>
      <div class="quote-mark">“</div>
      <p>Lorem ipsum dolor sit amet, consec tetur adipiscing elit, sed do eiusmod tempor incididunt ut labore et dolore magna aliqua. Ut enim ad minim veniam, quis nostrud exercitation ullamco laboris nisi ut aliquip ex ea commodo consequat</p>
      <div class="author"><div class="avatar" role="img" aria-label="Reviewer portrait"></div><div><b>Dana Reyes</b><small>2 days ago</small></div></div>
    </article>
    <article class="quote-card">
      <div class="quote-photo" role="img" aria-label="Busy restaurant kitchen line" style="background:linear-gradient(160deg,#8e969c,#3e4449)"></div>
      <div class="quote-mark">“</div>
      <p>Lorem ipsum dolor sit amet, consec tetur adipiscing elit, sed do eiusmod tempor incididunt ut labore et dolore magna aliqua. Ut enim ad minim veniam, quis nostrud exercitation ullamco laboris nisi ut aliquip ex ea commodo consequat</p>
      <div class="author"><div class="avatar" role="img" aria-label="Reviewer portrait"></div><div><b>Dana Reyes</b><small>2 days ago</small></div></div>
    </article>
    <article class="quote-card">
      <div class="quote-photo" role="img" aria-label="Plates being garnished for catering" style="background:linear-gradient(160deg,#e2e5e2,#8a968c)"></div>
      <div class="quote-mark">“</div>
      <p>Lorem ipsum dolor sit amet, consec tetur adipiscing elit, sed do eiusmod tempor incididunt ut labore et dolore magna aliqua. Ut enim ad minim veniam, quis nostrud exercitation ullamco laboris nisi ut aliquip ex ea commodo consequat</p>
      <div class="author"><div class="avatar" role="img" aria-label="Reviewer portrait"></div><div><b>Dana Reyes</b><small>2 days ago</small></div></div>
    </article>
  </div>
  <div class="pager"><i class="on"></i><i></i><i></i><i></i><i></i></div>
</section>

<section class="highlight">
  <div class="wordmark">KelvaTrix88</div>
  <blockquote>Tammo helped us reduce cooking times by 40%.</blockquote>
  <svg class="arrow" style="left:112px" width="36" height="66" viewBox="0 0 36 66" fill="none" stroke="#9aa0a8" stroke-width="3"><path d="M32 3L4 33l28 30"/></svg>
  <svg class="arrow" style="left:1052px" width="36" height="66" viewBox="0 0 36 66" fill="none" stroke="#9aa0a8" stroke-width="3"><path d="M4 3l28 30L4 63"/></svg>
</section>

<section class="video">
  <h2 class="section-title">WATCH TAMMO COOK A FULL<br>BATCH FROM <span class="accent">START TO FINISH.</span></h2>
  <div class="title-rule"></div>
  <div class="video-frame" role="img" aria-label="Video still of Tammo demonstrated at a trade show booth">
    <div class="play"><svg width="24" height="26" viewBox="0 0 24 26"><path d="M4 2l18 11L4 24z" fill="#fff"/></svg></div>
  </div>
</section>

<section class="cta">
  <div class="cta-product" role="img" aria-label="Tammo cooking robot unit"></div>
  <div class="cta-copy">
    <h2>TAMMO THE<br><span class="accent">COOKING ROBOT</span></h2>
    <div class="rule"></div>
    <p>Lorem ipsum dolor sit amet, consec tetur adipiscing elit, sed do eiusmod tempor incididunt ut labore et dolore magna aliqua. Ut enim ad minim veniam, quis nostrud exercitation ullamco.</p>
    <a class="btn btn-solid">Book a Demo</a>
  </div>
</section>

<footer class="site-footer">
  <div class="wordmark">KelvaTrix88</div>
  <div class="footer-col" style="left:437px">
    <h4>MENU</h4>
    <ul><li>Home</li><li>Product</li><li>Solutions</li><li>ROI / Economics</li><li>Case Studies</li><li>Pricing</li><li>About Us</li><li>Resources</li><li>Contact</li></ul>
  </div>
  <div class="footer-col" style="left:589px;width:270px">
    <h4>CONTACT US</h4>
    <div class="contact-line"><svg width="14" height="18" viewBox="0 0 14 18" fill="#fff"><path d="M7 0a7 7 0 0 1 7 7c0 5-7 11-7 11S0 12 0 7a7 7 0 0 1 7-7zm0 4a3 3 0 1 0 0 6 3 3 0 0 0 0-6z"/></svg><span>482 W Harbor Loop Ste 310,<br>Alvera Bay, CA, United States, 90817</span></div>
    <div class="contact-line"><svg width="14" height="14" viewBox="0 0 14 14" fill="#fff"><path d="M3 0l3 3-2 2c1 2 3 4 5 5l2-2 3 3-2 3C6 14 0 8 0 2z"/></svg><span>+1 (800) 555 0142</span></div>
    <div class="contact-line"><svg width="14" height="12" viewBox="0 0 14 12" fill="#fff"><path d="M0 0h14v12H0z"/><path d="M0 0l7 6 7-6" stroke="#0d2a5f" stroke-width="1.5" fill="none"/></svg><span>info@kelvatrix88.com</span></div>
  </div>
  <div class="footer-col" style="left:878px">
    <h4>FOLLOW US</h4>
    <div class="socials"><i></i><i></i><i></i><i></i><i></i></div>
    <a class="btn btn-solid">Request a Demo</a>
  </div>
  <div class="footer-rule"></div>
  <p class="legal">Privacy Policy || Terms of Service | KelvaTrix88 © 2025. All Rights Reserved.</p>
</footer>

</body>
</html>
```